The logo name is "Harbor Skin". The name of the product will be "Cutaneous Comfort". This product is specifically formulated for amputees. Therefore under the product name it should state "for amputees". The catch phrase will be "Experience Harbor find Calmness"
These are the things we need on the label:
Logo, product name, "for amputees", "Experience Harbor find Calmness", Safe, Effective, Directions: spray on problem areas, no need to dry off. harborskin.example, Made in Canada, 500ml.
The MOST IMPORTANT and therefore the most prominent thing on this lable will be the LOGO! The second most prominent thing will be the word "Comfort" We want to keep it very plain, very simple, very unclutered. Keep in mind that this lable will be placed on a white bottle or have a white back ground. The 500ml white PE bottle with trigger sprayer will have a tear drop label. See attached die line (S-294).
We want to stay with the colours that goes with the colour scheme of the logo. See attached logo. Soft colours. We do not want a picture! We would like the lable to be classy and rich.
Updates
The logo name is "Harbor Skin". The name of the product will be "Cutaneous Comfort". This product is specificlly formulated for amputees. Therefore under the product name it should state "for amputees". The catch phrase will be "Experience Harbor find Calmness"
Logo, product name, "for amputees", catch phrase "Experience Harbor find Calmness", Clean, Safe, Effective, Directions: spray on problem areas, no need to dry off. Also Harbor Skin Corpation, harborskin.example, Made in Canada, 500ml.
We want to stay with the colour scheme of the logo. See attached logo. Soft colours. We do not want a picture! We would like the lable to be classy and rich.
This is the offical directive that came from the governing panal of this lable. This panal it not know where it wanted to take this lable that would represent this line until they review all of your submissions, thank you for all your talented hard work. But now it is clear it is time to regroup and hit this objective.
Project Deadline Extended
Reason: New restrictions on lable wording for this product.
Target Market(s)
Amputees and Parents of.
Industry/Entity Type
Product
Requirements
Must have
- Final product to be in a pdf or an illustrator file

```html
<!DOCTYPE html>
<html lang="en">
<head>
<meta charset="utf-8">
<title>Cutaneous Comfort – Teardrop Label</title>
<link rel="stylesheet" href="https://fonts.googleapis.com/css2?family=Lobster&family=Tinos:ital,wght@0,400;0,700;1,400&display=swap">
<style>
  :root {
    --mint: #7ff5c9;
    --mint-soft: #c9f8e6;
    --mint-pale: #e6fcf3;
    --white: #ffffff;
    --orange: #f6b73c;
    --orange-deep: #e89a1c;
    --green: #0f7a3a;
    --green-dark: #0b5e2c;
    --die-line: #4a4a4a;
    --page: #ffffff;
  }
  html, body {
    margin: 0;
    padding: 0;
    width: 928px;
    height: 1200px;
    overflow: hidden;
    background: var(--page);
  }
  .canvas {
    position: relative;
    width: 928px;
    height: 1200px;
  }
  .label {
    position: absolute;
    left: 160px;
    top: 60px;
    width: 608px;
    height: 1080px;
  }
  .script {
    font-family: "Lobster", cursive;
    paint-order: stroke fill;
    stroke-linejoin: round;
  }
  .product-line {
    fill: var(--white);
    stroke: var(--orange);
    stroke-width: 3;
    font-size: 34px;
  }
  .product-hero {
    fill: var(--white);
    stroke: var(--orange);
    stroke-width: 5;
    font-size: 74px;
  }
  .audience {
    fill: var(--green-dark);
    stroke: var(--white);
    stroke-width: 3;
    font-size: 19px;
  }
  .tagline {
    font-family: "Tinos", serif;
    font-style: italic;
    fill: var(--white);
    font-size: 22px;
  }
  .claims {
    fill: var(--white);
    stroke: var(--green);
    stroke-width: 3;
    font-size: 21px;
  }
  .company {
    font-family: "Tinos", serif;
    fill: var(--orange);
    font-size: 11.5px;
  }
  .website {
    font-family: "Tinos", serif;
    font-weight: 700;
    fill: var(--orange);
    font-size: 20px;
  }
  .volume {
    fill: var(--orange);
    stroke: var(--white);
    stroke-width: 1;
    font-size: 19px;
  }
  .origin {
    font-family: "Tinos", serif;
    fill: var(--white);
    font-size: 12px;
  }
  .directions {
    font-family: "Tinos", serif;
    font-weight: 700;
    fill: var(--green-dark);
    font-size: 13.5px;
  }
  .brand-name {
    font-family: "Tinos", serif;
    fill: var(--green);
    font-size: 44px;
  }
</style>
</head>
<body>
<main class="canvas">
  <svg class="label" viewBox="0 0 405 720" xmlns="http://www.w3.org/2000/svg">
    <defs>
      <clipPath id="label-shape">
        <path d="M112,8 Q125,-2 138,8 C250,130 405,380 405,600 L405,680 Q405,720 365,720 L40,720 Q0,720 0,680 L0,480 C0,300 60,110 112,8 Z"/>
      </clipPath>
      <linearGradient id="leaf-tones" x1="0" y1="0" x2="1" y2="0">
        <stop offset="0" stop-color="var(--mint-pale)"/>
        <stop offset="0.6" stop-color="var(--mint-soft)"/>
        <stop offset="1" stop-color="var(--mint)"/>
      </linearGradient>
    </defs>

    <g clip-path="url(#label-shape)">
      <rect class="label-ground" x="0" y="0" width="405" height="720" fill="var(--mint)"/>
      <path class="white-sweep" d="M405,300 C300,330 170,400 120,520 L100,600 L405,600 Z" fill="var(--white)"/>
      <path class="leaf-art" role="img" aria-label="Soft mint leaf shapes decoration"
            d="M140,600 C150,520 220,465 300,455 C350,450 390,470 405,490 L405,600 Z"
            fill="url(#leaf-tones)" opacity="0.85"/>
      <path class="lower-band" d="M0,537 Q170,615 405,596 L405,720 L0,720 Z" fill="var(--white)"/>
      <path class="accent-curve" d="M0,537 Q170,615 405,596" fill="none" stroke="var(--orange)" stroke-width="3"/>
    </g>

    <path class="die-line" d="M112,8 Q125,-2 138,8 C250,130 405,380 405,600 L405,680 Q405,720 365,720 L40,720 Q0,720 0,680 L0,480 C0,300 60,110 112,8 Z"
          fill="none" stroke="var(--die-line)" stroke-width="1"/>

    <text class="script product-line" x="50" y="156">Cutaneous</text>
    <text class="script product-hero" x="48" y="230">Comfort</text>
    <text class="script audience" x="88" y="255">for amputees</text>

    <text class="tagline" x="30" y="299">Experience Harbor</text>
    <text class="tagline" x="30" y="325">find Calmness</text>
    <text class="script claims" x="28" y="361">Clean, Safe, Effective</text>

    <text class="company" x="370" y="403" text-anchor="end">Harbor Skin Corpation</text>
    <text class="website" x="370" y="428" text-anchor="end">harborskin.example</text>

    <text class="script volume" x="8" y="506">500ml</text>
    <text class="origin" x="8" y="523">Made in Canada</text>

    <text class="directions" x="397" y="550" text-anchor="end">Directions:</text>
    <text class="directions" x="397" y="569" text-anchor="end">spray on problem areas, no need to dry off.</text>

    <g class="brand-mark">
      <rect class="brand-square" x="44" y="614" width="48" height="48" fill="var(--orange)"/>
      <text class="brand-name" x="104" y="660">Harbor Skin</text>
    </g>
  </svg>
</main>
</body>
</html>
```